Dalvick's Business Card

I need some designs for a new business card including the new logo attached. An old example of our business card is also attached to show all the data that should be included on the new design.
**I added some more examples someone had mocked up**

Contact Information for Business Card

Should include all info on other examples uploaded.

```html
<!DOCTYPE html>
<html lang="en">
<head>
<meta charset="utf-8">
<title>Dalvick's Business Card</title>
<link rel="stylesheet" href="https://fonts.googleapis.com/css2?family=Barlow+Condensed:wght@600;700&family=Montserrat:wght@600;700&family=Open+Sans:wght@400;500&display=swap">
<style>
  :root {
    --page: #e4e4e4;
    --blue: #0a6fb4;
    --red: #e31e25;
    --white: #ffffff;
    --paper: #f4f4f4;
  }
  * { margin: 0; padding: 0; box-sizing: border-box; }
  html, body { width: 1200px; height: 960px; overflow: hidden; background: var(--page); }
  .card {
    position: absolute; left: 295px; width: 614px; height: 350px; overflow: hidden;
  }
  .card-front { top: 107px; background: var(--blue); }
  .card-back { top: 512px; background: var(--paper); }
  .card svg.waves { position: absolute; inset: 0; width: 614px; height: 350px; }

  .front-headline, .front-tagline {
    position: absolute; left: 0; width: 100%; text-align: center; white-space: nowrap;
    font-family: "Barlow Condensed", sans-serif; font-weight: 700; color: var(--white);
  }
  .front-headline { top: 20px; font-size: 22.5px; letter-spacing: 0.4px; }
  .front-tagline { top: 298px; font-size: 23.5px; }
  .front-brand {
    position: absolute; left: 0; width: 100%; top: 222px;
    display: flex; justify-content: center; align-items: center; gap: 12px;
  }
  .front-brand .mark { width: 34px; height: 34px; border-radius: 50%; background: var(--white); }
  .front-brand .name {
    font-family: "Barlow Condensed", sans-serif; font-weight: 700; font-size: 50px;
    color: var(--white); line-height: 1;
  }

  .back-brand {
    position: absolute; left: 48px; top: 48px; display: flex; align-items: center; gap: 14px;
  }
  .back-brand .mark { width: 66px; height: 66px; border-radius: 50%; background: var(--red); }
  .back-brand .name {
    font-family: "Montserrat", sans-serif; font-weight: 700; font-size: 46px;
    color: var(--blue); line-height: 1;
  }
  .person { position: absolute; left: 131px; top: 152px; font-family: "Montserrat", sans-serif; }
  .person .person-name { font-weight: 700; font-size: 21px; color: var(--blue); }
  .person .person-role { font-family: "Open Sans", sans-serif; font-size: 16px; color: var(--red); margin-top: 2px; }
  .contact {
    position: absolute; left: 131px; top: 274px; list-style: none;
    font-family: "Open Sans", sans-serif; font-size: 17px; color: var(--white);
  }
  .contact li { display: flex; align-items: center; gap: 6px; height: 24px; }
  .contact svg { width: 16px; height: 16px; }
</style>
</head>
<body>

<section class="card card-front">
  <svg class="waves" viewBox="0 0 614 350" aria-hidden="true">
    <path fill="var(--white)" d="M0 148 C150 128 250 190 400 208 C500 220 570 170 614 138 L614 350 L0 350Z"/>
    <path fill="var(--red)" d="M0 168 C150 150 250 212 400 226 C500 236 570 192 614 170 L614 350 L0 350Z"/>
  </svg>
  <p class="front-headline">LICENSED &amp; INSURED &nbsp;|&nbsp; FAMILY OWNED &amp; OPERATED</p>
  <div class="front-brand">
    <span class="mark"></span>
    <span class="name">DALVICK'S</span>
  </div>
  <p class="front-tagline">Call Today For All Your Hvac, Refrigeration &amp; Plumbing Needs</p>
</section>

<section class="card card-back">
  <svg class="waves" viewBox="0 0 614 350" aria-hidden="true">
    <path fill="var(--red)" d="M0 253 C100 226 200 214 300 222 C420 234 500 298 560 310 C590 316 605 304 614 288 L614 350 L0 350Z"/>
    <path fill="var(--white)" d="M0 282 C100 246 200 232 300 240 C420 252 500 308 560 316 C590 320 605 310 614 296 L614 350 L0 350Z"/>
    <path fill="var(--blue)" d="M0 290 C100 254 200 240 300 248 C420 260 500 316 560 324 C590 328 605 318 614 304 L614 350 L0 350Z"/>
  </svg>
  <div class="back-brand">
    <span class="mark"></span>
    <span class="name">DALVICK'S</span>
  </div>
  <div class="person">
    <p class="person-name">ETHAN DALVICK</p>
    <p class="person-role">CO-OWNER</p>
  </div>
  <ul class="contact">
    <li>
      <svg viewBox="0 0 24 24" aria-hidden="true"><path fill="var(--white)" d="M6.6 10.8a15.1 15.1 0 0 0 6.6 6.6l2.2-2.2a1 1 0 0 1 1-.25 11.4 11.4 0 0 0 3.6.57 1 1 0 0 1 1 1V20a1 1 0 0 1-1 1A17 17 0 0 1 3 4a1 1 0 0 1 1-1h3.5a1 1 0 0 1 1 1c0 1.25.2 2.45.57 3.6a1 1 0 0 1-.25 1z"/></svg>
      555.014.2286
    </li>
    <li>
      <svg viewBox="0 0 24 24" aria-hidden="true"><rect x="2.5" y="5" width="19" height="14" fill="none" stroke="var(--white)" stroke-width="2"/><path d="M3 6l9 7 9-7" fill="none" stroke="var(--white)" stroke-width="2"/></svg>
      hvacdalvick@example.com
    </li>
  </ul>
</section>

</body>
</html>
```